Birchline Septic Solutions

Would like to see some single sided ones but would also like to see some double sided with one sided only being the logo. Owners name is Colin Vandro. Phone number is 555-214-0387
Services are pumping, inspections, installs, and repairs

Contact Information for Business Card

555-241-0387 Colin Vandro Alderbrook, OH

```html
<!DOCTYPE html>
<html lang="en">
<head>
<meta charset="utf-8">
<title>Birchline Septic Solutions – Business Card</title>
<link rel="stylesheet" href="https://fonts.googleapis.com/css2?family=Montserrat:wght@500;700;800&display=swap">
<style>
  :root {
    --page-bg: #e6e3e3;
    --card-bg: #f5f2f2;
    --ink: #111111;
    --ink-soft: #2a2a2a;
    --teal: #2bbdb9;
    --rule: #8f8b8b;
    --black: #000000;
  }
  * { box-sizing: border-box; margin: 0; padding: 0; }
  html, body {
    width: 1200px; height: 900px; overflow: hidden;
    background: var(--page-bg);
    font-family: "Montserrat", sans-serif;
  }
  .business-card {
    position: absolute; left: 100px; top: 140px;
    width: 1000px; height: 620px;
    background: var(--card-bg);
    overflow: hidden;
    box-shadow: 0 12px 34px rgba(0,0,0,0.16);
  }
  .brand-name {
    position: absolute; left: 92px; top: 232px; width: 360px;
    font-weight: 700; font-size: 30px; line-height: 1.35;
    letter-spacing: 0.04em; color: var(--ink);
    text-align: center;
  }
  .brand-divider {
    position: absolute; left: 500px; top: 166px;
    width: 2px; height: 268px; background: var(--rule);
  }
  .owner-name {
    position: absolute; left: 542px; top: 208px;
    font-weight: 800; font-size: 34px; letter-spacing: 0.01em;
    color: var(--ink);
  }
  .contact-line {
    position: absolute; left: 542px;
    display: flex; align-items: center; gap: 14px;
    font-weight: 500; font-size: 28px; letter-spacing: 0.04em;
    color: var(--ink);
  }
  .contact-line svg { width: 26px; height: 30px; flex: none; }
  .contact-phone { top: 302px; }
  .contact-location { top: 348px; }
  .service-list {
    position: absolute; left: 142px; top: 470px;
    display: flex; gap: 32px; list-style: none;
    font-weight: 500; font-size: 28px; letter-spacing: 0.01em;
    color: var(--ink);
  }
  .card-waves { position: absolute; left: 0; top: 0; width: 1000px; height: 620px; }
  .wave-teal { fill: var(--teal); }
  .wave-black { fill: var(--black); }
</style>
</head>
<body>
  <div class="business-card">
    <div class="brand-name">BIRCHLINE<br>SEPTIC SOLUTIONS</div>
    <div class="brand-divider"></div>

    <div class="owner-name">COLIN VANDRO</div>

    <div class="contact-line contact-phone">
      <svg viewBox="0 0 24 24" aria-hidden="true">
        <path fill="var(--teal)" d="M6.6 10.8a15.1 15.1 0 0 0 6.6 6.6l2.2-2.2a1 1 0 0 1 1-.25 11.4 11.4 0 0 0 3.6.57 1 1 0 0 1 1 1V20a1 1 0 0 1-1 1A17 17 0 0 1 3 4a1 1 0 0 1 1-1h3.5a1 1 0 0 1 1 1c0 1.25.2 2.45.57 3.57a1 1 0 0 1-.25 1z"/>
        <path fill="none" stroke="var(--teal)" stroke-width="1.6" stroke-linecap="round" d="M14 3.5a7 7 0 0 1 6.5 6.5M14 7a3.5 3.5 0 0 1 3 3"/>
      </svg>
      <span>555-214-0387</span>
    </div>

    <div class="contact-line contact-location">
      <svg viewBox="0 0 24 28" aria-hidden="true">
        <path fill="var(--teal)" d="M12 1a9 9 0 0 0-9 9c0 6.8 9 17 9 17s9-10.2 9-17a9 9 0 0 0-9-9zm0 12.3a3.3 3.3 0 1 1 0-6.6 3.3 3.3 0 0 1 0 6.6z"/>
      </svg>
      <span>Alderbrook, OH</span>
    </div>

    <ul class="service-list">
      <li>PUMPING</li>
      <li>INSPECTIONS</li>
      <li>INSTALLS</li>
      <li>REPAIRS</li>
    </ul>

    <svg class="card-waves" viewBox="0 0 1000 620" aria-hidden="true">
      <path class="wave-teal" d="M0 500 C 140 545, 330 585, 540 548 C 360 592, 150 582, 0 540 Z"/>
      <path class="wave-black" d="M0 552 C 180 602, 420 605, 600 548 C 740 505, 880 515, 1000 540 L1000 620 L0 620 Z"/>
    </svg>
  </div>
</body>
</html>
```